Concierge Dental / Medical Supply Ordering Business - Sleek, Efficient, Professional, Elite

www.brantonkeelmedical.com - example website.

We are a concierge supply ordering business for medical and dental that provide DSO price savings on supplies while maintaining business autonomy and independence.

We want a very simple website that looks very professional says what we do and gives a very simple method to contact us & sign up as above.

Target Market(s)

Independent Dental and Medical Practices

Industry/Entity Type

Dental and Medical - healthcare

Coding

Coded - Design and coding required

Number of Pages Required

3 page

Font styles to use
Sans Serif

Colors
0054AA
0677BA
7BADD7
CADEEF
E8F1F8

Requirements
Must have
• Simple contact page, sleek efficient design, uncomplicated.
Nice to have
• Sign up page vs just a contact page.
Should not have
• Lots of pages, hard to navigate,

```html
<!DOCTYPE html>
<html lang="en">
<head>
<meta charset="utf-8">
<title>Brantonkeel Supply — Supply Ordering for Medical and Dental</title>
<link href="https://fonts.googleapis.com/css2?family=Mulish:wght@400;600;700&display=swap" rel="stylesheet">
<style>
:root{
  --blue-deep:#0054AA;
  --blue:#0677BA;
  --blue-btn:#2f6fa3;
  --blue-mid:#7BADD7;
  --blue-light:#CADEEF;
  --blue-pale:#E8F1F8;
  --band-blue:#1f5f97;
  --charcoal:#474747;
  --ink:#2b2b2b;
  --text:#555;
  --white:#fff;
  --black:#000;
}
*{box-sizing:border-box;margin:0;padding:0}
html,body{width:1200px;height:2896px;overflow:hidden}
body{font-family:"Mulish",sans-serif;color:var(--ink);background:var(--white)}
a{color:inherit;text-decoration:none}
.btn{display:inline-block;background:var(--blue-btn);color:var(--white);font-weight:600;font-size:15px;padding:12px 26px;border-radius:6px}

/* hero */
.hero{position:relative;height:548px;background:linear-gradient(180deg,#c9d4dc 0%,#9fb1bf 45%,#6d7f8e 100%);overflow:hidden}
.hero-shade{position:absolute;inset:0;background:linear-gradient(180deg,rgba(30,40,50,.15),rgba(20,30,40,.45))}
.nav{position:absolute;top:0;left:0;right:0;height:100px;display:flex;align-items:center;justify-content:space-between;padding:0 160px}
.brand{display:flex;align-items:center;gap:10px;color:var(--white);font-weight:700;font-size:18px}
.brand-square{width:34px;height:34px;border:3px solid var(--white);border-radius:4px}
.nav-links{display:flex;gap:8px;list-style:none;margin-top:-40px}
.nav-links a{display:block;color:var(--white);font-size:15px;padding:8px 12px;border-radius:4px}
.nav-links a.active{background:var(--blue-btn)}
.hero-content{position:absolute;top:248px;left:0;right:0;text-align:center;color:var(--white)}
.hero-title{font-size:38px;font-weight:700;margin-bottom:40px;text-shadow:0 2px 6px rgba(0,0,0,.3)}

/* mission */
.mission{height:542px;position:relative}
.mission-photo{position:absolute;left:0;top:62px;width:550px;height:410px;background:linear-gradient(135deg,#dfe8ef,#9cb4c6 55%,#6f8ea6)}
.mission-copy{position:absolute;left:596px;top:58px;width:470px}
.mission-title{font-size:36px;font-weight:400;line-height:1.2;color:var(--ink)}
.rule{width:70px;height:2px;background:#999;margin:26px 0 22px}
.body-text{font-size:14px;line-height:1.55;color:var(--text)}
.mission-copy .btn{margin-top:62px}

/* practice */
.practice{height:590px;background:var(--charcoal);color:var(--white);text-align:center;padding-top:58px}
.section-title{font-size:36px;font-weight:400}
.practice .rule{background:var(--white);margin:16px auto 0}
.cards{display:flex;justify-content:center;gap:32px;margin-top:80px}
.card{width:292px;height:380px;border:1px solid #8a8a8a;border-radius:10px;padding:34px 30px 0;display:flex;flex-direction:column;align-items:center}
.card-icon{width:70px;height:70px}
.card-title{font-size:18px;font-weight:700;margin:16px 0 6px}
.card .body-text{color:#e6e6e6;font-size:13px}
.card .btn{margin-top:26px;padding:9px 24px;font-size:14px}

/* initiatives */
.initiatives{position:relative;height:540px;background:linear-gradient(100deg,#a9cfe4 0%,#8ec3de 40%,#7bb8d8 100%);overflow:hidden}
.initiatives-photo{position:absolute;right:0;top:0;width:720px;height:540px;background:linear-gradient(120deg,rgba(255,255,255,0) 0%,rgba(232,241,248,.35) 50%,rgba(202,222,239,.5) 100%)}
.initiatives-copy{position:absolute;left:130px;top:40px;width:470px}
.initiatives-copy .rule{background:var(--ink);margin:18px 0 24px}
.initiatives-copy .body-text{color:#2e3d48}
.initiatives-copy .btn{margin-top:40px}

/* contact */
.contact{height:340px;background:var(--band-blue);color:var(--white);text-align:center;padding-top:58px}
.contact .section-title{font-size:46px}
.contact .body-text{color:var(--white);font-size:17px;width:560px;margin:26px auto 28px}
.contact .btn{background:var(--blue);padding:13px 30px}

/* footer */
.footer{height:336px;background:var(--black);color:var(--white);text-align:center;padding-top:100px}
.footer .brand{justify-content:center}
.footer-links{display:flex;justify-content:center;gap:28px;list-style:none;margin-top:42px;font-size:14px}
.copyright{font-size:11px;margin-top:30px;color:#ddd}
</style>
</head>
<body>

<header class="hero">
  <div class="hero-shade" role="img" aria-label="Bright dental treatment room with patient chair and equipment"></div>
  <nav class="nav">
    <a class="brand" href="#"><span class="brand-square"></span>Brantonkeel Supply</a>
    <ul class="nav-links">
      <li><a class="active" href="#">Home</a></li>
      <li><a href="#">About Us</a></li>
      <li><a href="#">Areas of Practice</a></li>
      <li><a href="#">FAQs</a></li>
      <li><a href="#">Contact us</a></li>
    </ul>
  </nav>
  <div class="hero-content">
    <h1 class="hero-title">Supply Ordering Business for Medical and Dental</h1>
    <a class="btn" href="#">Contact Us</a>
  </div>
</header>

<section class="mission">
  <div class="mission-photo" role="img" aria-label="Medical supply warehouse aisle with stocked shelves"></div>
  <div class="mission-copy">
    <h2 class="mission-title">Advocating for financial transparency in the medical supply world.</h2>
    <div class="rule"></div>
    <p class="body-text">Lorem ipsum dolor sit amet, consectetur adipiscing elit, sed do eiusmod tempor incididunt ut labore et dolore magna aliqua. Ut enim ad minim veniam, quis nostrud exercitation ullamco laboris nisi ut aliquip ex ea commodo consequat. Duis aute irure dolor in reprehenderit in voluptate velit esse cillum dolore eu fugiat nulla.</p>
    <a class="btn" href="#">Learn More</a>
  </div>
</section>

<section class="practice">
  <h2 class="section-title">Areas of Practice</h2>
  <div class="rule"></div>
  <div class="cards">
    <article class="card">
      <svg class="card-icon" viewBox="0 0 70 70" role="img" aria-label="Distribution icon"><circle cx="35" cy="35" r="26" fill="none" stroke="#fff" stroke-width="2"/><rect x="24" y="26" width="22" height="18" fill="none" stroke="#fff" stroke-width="2"/></svg>
      <h3 class="card-title">Distribution</h3>
      <p class="body-text">Lorem ipsum dolor sit amet, consectetur adipiscing elit, sed do eiusmod tempor incididunt ut labore et dolore magna aliqua. Ut enim ad minim veniam.</p>
      <a class="btn" href="#">Learn More</a>
    </article>
    <article class="card">
      <svg class="card-icon" viewBox="0 0 70 70" role="img" aria-label="Pharma icon"><rect x="18" y="14" width="34" height="42" rx="4" fill="none" stroke="#fff" stroke-width="2"/><path d="M35 26v18M26 35h18" stroke="#fff" stroke-width="2"/></svg>
      <h3 class="card-title">Pharma</h3>
      <p class="body-text">Lorem ipsum dolor sit amet, consectetur adipiscing elit, sed do eiusmod tempor incididunt ut labore et dolore magna aliqua. Ut enim ad minim veniam.</p>
      <a class="btn" href="#">Learn More</a>
    </article>
    <article class="card">
      <svg class="card-icon" viewBox="0 0 70 70" role="img" aria-label="Dental equipment icon"><path d="M20 12v46M35 12v46M50 12v46" stroke="#fff" stroke-width="2"/><circle cx="20" cy="14" r="4" fill="none" stroke="#fff" stroke-width="2"/><circle cx="50" cy="14" r="4" fill="none" stroke="#fff" stroke-width="2"/></svg>
      <h3 class="card-title">Dental Equipment</h3>
      <p class="body-text">Lorem ipsum dolor sit amet, consectetur adipiscing elit, sed do eiusmod tempor incididunt ut labore et dolore magna aliqua. Ut enim ad minim veniam.</p>
      <a class="btn" href="#">Learn More</a>
    </article>
  </div>
</section>

<section class="initiatives">
  <div class="initiatives-photo" role="img" aria-label="Pill bottles, syringes and medicine blister packs on a light blue surface"></div>
  <div class="initiatives-copy">
    <h2 class="mission-title">10 Initiatives to consider in your supply management execution</h2>
    <div class="rule"></div>
    <p class="body-text">Lorem ipsum dolor sit amet, consectetur adipiscing elit, sed do eiusmod tempor incididunt ut labore et dolore magna aliqua. Ut enim ad minim veniam, quis nostrud exercitation ullamco laboris nisi ut aliquip ex ea commodo consequat.</p>
    <a class="btn" href="#">Learn More</a>
  </div>
</section>

<section class="contact">
  <h2 class="section-title">Get in Touch</h2>
  <p class="body-text">For all questions, inquiries regarding our services, or assistance in referring someone to us. Please contact us below.</p>
  <a class="btn" href="#">Contact us</a>
</section>

<footer class="footer">
  <a class="brand" href="#"><span class="brand-square"></span>Brantonkeel Supply</a>
  <ul class="footer-links">
    <li><a href="#">Home</a></li>
    <li><a href="#">About Us</a></li>
    <li><a href="#">Areas of Practice</a></li>
    <li><a href="#">FAQs</a></li>
    <li><a href="#">Contact us</a></li>
  </ul>
  <p class="copyright">Copyright © 2023 All Rights Reserved</p>
</footer>

</body>
</html>
```